Wildlfower Field Guide Needs a Book Cover Design

We need a book cover design in formats compatible with Adobe Illustrator and/or Photoshop (vector file that can be edited). I have attached a Power Point file with the general design features for the front and back covers and photographs to be used in the book cover. The cover size is 6" wide by 9" high (same size as the attached Power Point file). The book cover should have the same format including photos as the attached file with a similar color scheme. We are looking for a sky blue background then title text in a complementary darker blue. The other color elements (borders around photos) can be the same darker blue or dark gray. We are looking for better text types/styles for the title than those is the attached file. All three lines of the title should have the same width (1st line - thicker text, 2nd line - white italics on dark background, 3rd line - narrow text). The dark background on the 2nd line would ideally have some texture or style like a trail. On the back cover, written paragraphs should remain in Ebrima font.

Requirements
Must have
• Project should follow general cover outline of attached Power Point file
• Should have desired color scheme
• Must include all photos as formatted in the attached in the Power point file
Nice to have
• The title (2nd line) can be a solid color matching 1st line text or texture like a hiking trail

```html
<!DOCTYPE html>
<html lang="en">
<head>
<meta charset="utf-8">
<title>Desert Blooms Beside the Path – Cover</title>
<link rel="stylesheet" href="https://fonts.googleapis.com/css2?family=Source+Sans+3:ital,wght@0,400;0,600;0,700;0,800;1,600&family=Noto+Sans:wght@400;700&display=swap">
<style>
  :root {
    --sky: #cfe4f8;
    --title-blue: #2b7fdc;
    --band-blue: #2565c9;
    --band-blue-dark: #1d55b0;
    --frame-blue: #2a78d6;
    --ink: #1c1c1c;
    --white: #ffffff;
  }
  * { box-sizing: border-box; margin: 0; padding: 0; }
  html, body { width: 1200px; height: 864px; overflow: hidden; background: var(--sky); }
  .cover {
    position: relative; width: 1200px; height: 864px; background: var(--sky);
    font-family: "Source Sans 3", "Source Sans Pro", sans-serif;
  }

  .title-block { position: absolute; top: 40px; width: 486px; height: 215px; overflow: visible; }
  .title-block.back { left: 54px; }
  .title-block.front { left: 672px; }
  .title-main { fill: var(--title-blue); font-family: "Source Sans 3", sans-serif; font-weight: 800; font-size: 74px; }
  .title-band-text { fill: var(--white); font-family: "Source Sans 3", sans-serif; font-style: italic; font-weight: 600; font-size: 66px; }
  .title-sub { fill: var(--title-blue); font-family: "Source Sans 3", sans-serif; font-weight: 600; font-size: 50px; }

  .back-panel {
    position: absolute; left: 54px; top: 283px; width: 487px; height: 534px;
    border: 3px solid var(--frame-blue);
  }
  .photo-column {
    position: absolute; left: 0; top: 0; width: 149px; height: 444px;
    border-right: 3px solid var(--frame-blue);
    display: flex; flex-direction: column; gap: 3px; background: var(--frame-blue);
  }
  .photo-column .photo { flex: 1; }
  .blurb {
    position: absolute; left: 173px; top: 14px; width: 296px;
    font-family: "Noto Sans", sans-serif; font-size: 16.5px; line-height: 24.2px; color: var(--ink);
  }
  .blurb strong { font-weight: 700; }
  .bio {
    position: absolute; left: 0; top: 444px; width: 100%; height: 84px;
    border-top: 3px solid var(--frame-blue);
    padding: 11px 14px 0 14px;
    font-family: "Noto Sans", sans-serif; font-size: 11.5px; line-height: 15.5px; color: var(--ink);
  }
  .bio p { width: 292px; }

  .spine { position: absolute; left: 574px; top: 40px; width: 52px; height: 780px; overflow: visible; }
  .spine-title { fill: var(--ink); font-family: "Source Sans 3", sans-serif; font-weight: 800; font-size: 24px; }
  .spine-author { fill: var(--title-blue); font-family: "Source Sans 3", sans-serif; font-weight: 800; font-size: 24px; }

  .photo-grid {
    position: absolute; left: 672px; top: 282px; width: 485px; height: 484px;
    border: 4px solid var(--frame-blue); background: var(--frame-blue);
    display: grid; grid-template-columns: repeat(3, 1fr); grid-template-rows: repeat(3, 1fr); gap: 4px;
  }
  .author-name {
    position: absolute; left: 672px; top: 778px; width: 486px; text-align: center;
    color: var(--title-blue); font-weight: 700; font-size: 46px; line-height: 56px;
  }

  .photo { display: block; width: 100%; height: 100%; }
  .photo.yellow-cactus { background: radial-gradient(circle at 50% 45%, #f1d64a, #c9a22a 55%, #6b5a3a); }
  .photo.red-cactus { background: radial-gradient(circle at 50% 50%, #f07a6a, #d8434a 45%, #6a3a2e); }
  .photo.deep-cactus { background: radial-gradient(circle at 50% 50%, #e8565f, #b9263a 45%, #4a4a3e); }
  .photo.flower-a { background: radial-gradient(circle at 50% 50%, #e9c71a 0 38%, #4a4a36 60%); }
  .photo.flower-b { background: radial-gradient(circle at 50% 50%, #f0cb16 0 36%, #5a5346 62%); }
  .photo.flower-c { background: radial-gradient(circle at 50% 50%, #e6d86a 0 40%, #4c5638 64%); }
  .photo.flower-d { background: radial-gradient(circle at 50% 50%, #efbe2a 0 40%, #8a8a7a 66%); }
  .photo.flower-e { background: radial-gradient(circle at 50% 50%, #f2d125 0 36%, #5e5a4c 62%); }
  .photo.flower-f { background: radial-gradient(circle at 50% 50%, #e8c428 0 32%, #6e6a5a 60%); }
  .photo.flower-g { background: radial-gradient(circle at 50% 50%, #f4d214 0 44%, #b8ae9a 70%); }
  .photo.flower-h { background: radial-gradient(circle at 50% 50%, #f6d40e 0 44%, #8a8270 70%); }
  .photo.flower-i { background: radial-gradient(circle at 50% 50%, #f3cc12 0 40%, #7a7468 68%); }
</style>
</head>
<body>
<main class="cover">

  <svg class="title-block back" viewBox="0 0 486 215" aria-label="Desert Blooms Beside the Path, Arizona Sonoran Desert">
    <defs>
      <linearGradient id="band-fill" x1="0" x2="1" y1="0" y2="0">
        <stop offset="0" stop-color="#1d55b0"/>
        <stop offset="0.5" stop-color="#2565c9"/>
        <stop offset="1" stop-color="#1d55b0"/>
      </linearGradient>
    </defs>
    <text class="title-main" x="1" y="58" textLength="484" lengthAdjust="spacingAndGlyphs">DESERT BLOOMS</text>
    <rect x="0" y="72" width="486" height="89" fill="url(#band-fill)"/>
    <text class="title-band-text" x="243" y="137" text-anchor="middle" textLength="420" lengthAdjust="spacingAndGlyphs">Beside the Path</text>
    <text class="title-sub" x="1" y="207" textLength="484" lengthAdjust="spacingAndGlyphs">Arizona Sonoran Desert</text>
  </svg>

  <section class="back-panel">
    <div class="photo-column">
      <div class="photo yellow-cactus" role="img" aria-label="Photo of a yellow cactus flower"></div>
      <div class="photo red-cactus" role="img" aria-label="Photo of a red cactus flower with spines"></div>
      <div class="photo deep-cactus" role="img" aria-label="Photo of a deep red cactus flower"></div>
    </div>
    <p class="blurb">Desert Blooms Beside the Path: Arizona Sonoran Desert is a pocket companion that pairs clear photographs with short notes on 160 wildflowers hikers are likely to meet on Sonoran Desert trails. It was written for walkers, families and curious naturalists who want to put a name to the color they spot beside the path. Every species included is a familiar sight in the preserves and open spaces surrounding Phoenix and Tucson. Flowers are grouped by color, form and size, so one glance at a bloom leads straight to its page and settles the question: <strong>Which desert flower is this?</strong></p>
    <div class="bio"><p>Daniel Hartwell studied field ecology and has walked countless desert miles across the Arizona Sonoran Desert, learning its native plants and photographing its seasonal wildflowers.</p></div>
  </section>

  <svg class="spine" viewBox="0 0 52 780" aria-label="Desert Blooms Beside the Path Arizona Sonoran Desert, Hartwell">
    <text class="spine-title" transform="translate(17,0) rotate(90)" x="0" y="0" textLength="620" lengthAdjust="spacingAndGlyphs">DESERT BLOOMS BESIDE THE PATH ARIZONA SONORAN DESERT</text>
    <text class="spine-author" transform="translate(17,0) rotate(90)" x="672" y="0" textLength="106" lengthAdjust="spacingAndGlyphs">HARTWELL</text>
  </svg>

  <svg class="title-block front" viewBox="0 0 486 215" aria-label="Desert Blooms Beside the Path, Arizona Sonoran Desert">
    <text class="title-main" x="1" y="58" textLength="484" lengthAdjust="spacingAndGlyphs">DESERT BLOOMS</text>
    <rect x="0" y="72" width="486" height="89" fill="url(#band-fill)"/>
    <text class="title-band-text" x="243" y="137" text-anchor="middle" textLength="420" lengthAdjust="spacingAndGlyphs">Beside the Path</text>
    <text class="title-sub" x="1" y="207" textLength="484" lengthAdjust="spacingAndGlyphs">Arizona Sonoran Desert</text>
  </svg>

  <section class="photo-grid">
    <div class="photo flower-a" role="img" aria-label="Photo of a four-petaled yellow desert flower"></div>
    <div class="photo flower-b" role="img" aria-label="Photo of a bright yellow four-petaled flower"></div>
    <div class="photo flower-c" role="img" aria-label="Photo of a pale yellow four-petaled flower"></div>
    <div class="photo flower-d" role="img" aria-label="Photo of a yellow five-petaled flower"></div>
    <div class="photo flower-e" role="img" aria-label="Photo of a yellow five-petaled desert flower"></div>
    <div class="photo flower-f" role="img" aria-label="Photo of a yellow flower with narrow petals"></div>
    <div class="photo flower-g" role="img" aria-label="Photo of a yellow daisy-like flower"></div>
    <div class="photo flower-h" role="img" aria-label="Photo of a yellow daisy with orange center"></div>
    <div class="photo flower-i" role="img" aria-label="Photo of a yellow many-rayed daisy"></div>
  </section>

  <div class="author-name">Daniel Hartwell</div>

</main>
</body>
</html>
```